K7 Electrical Services Ltd Web design

I require a web site for my new electrical contracting company. We are customer service orientated. Offering high value electrical installations, design and maintenance. Focused on custom residential and commercial upgrading. Lighting design and application are paramount in our company's services. Industry leading product use and integration are always on the forefront with our customer client services. As well as energy efficiency.

Target Market(s)

Homebuilders, General Contractors, Property management companies, clients, individuals,

Industry/Entity Type

Electric Company

Coding

Coded - Design and coding required

Number of Pages Required

3 page

Requirements
Must have
• Classic, modern, edgy but not trendy . Appeals to the masse.
• 3 page
• home page
• about page
• gallery page
• ability to contact from the webiste
Nice to have
• open to all types of designs that are relative to the construction industry.
• Black, Grey, metallic ice blue and deep purple colours from the logo.
Should not have
• anything cheesy with cartoon light bulb images.

```html
<!DOCTYPE html>
<html lang="en">
<head>
<meta charset="utf-8">
<title>K7 Electrical Services Ltd</title>
<link rel="stylesheet" href="https://fonts.googleapis.com/css2?family=Poppins:ital,wght@0,400;0,500;0,600;0,700;1,400&family=Open+Sans:wght@400;600&display=swap">
<style>
:root{
  --purple:#5b2a93;
  --purple-deep:#4a1f7e;
  --purple-soft:#7a4bb0;
  --ink:#222222;
  --body:#7a7a7a;
  --black:#0b0b0b;
  --white:#ffffff;
  --grey-date:#6b6b6b;
  --star:#f4c21a;
}
*{margin:0;padding:0;box-sizing:border-box}
html,body{width:1200px;height:2932px;overflow:hidden}
body{position:relative;background:var(--white);font-family:"Open Sans",Arial,sans-serif;color:var(--ink)}
.abs{position:absolute}
a{color:inherit;text-decoration:none}

/* header */
.hero-photo{left:0;top:0;width:1200px;height:600px;background:linear-gradient(115deg,#d9d4cc 0%,#b9aea0 30%,#8a7f74 52%,#c9c1b6 70%,#e6e2dc 100%)}
.header{left:0;top:0;width:1200px;height:166px;background:rgba(255,255,255,.86)}
.brand{left:86px;top:42px;font-family:"Poppins",sans-serif;font-weight:600;font-size:30px;color:var(--purple);letter-spacing:1px;display:flex;align-items:center;gap:12px}
.brand-mark{width:22px;height:22px;border-radius:50%;background:var(--purple)}
.contact-top{top:40px;display:flex;align-items:center;gap:12px}
.contact-top .ring{width:38px;height:38px;border:3px solid var(--purple);border-radius:50%;display:flex;align-items:center;justify-content:center}
.contact-top small{display:block;font-size:10px;color:#555}
.contact-top b{display:block;font-family:"Poppins",sans-serif;font-weight:500;font-size:19px;color:#333;line-height:1.1}
.socials{display:flex;gap:18px;align-items:center}
.socials span{width:14px;height:14px;border:2px solid #555;border-radius:3px;display:block}
.nav{left:0;top:128px;width:1200px;height:30px;font-size:13.5px;color:#555}
.nav a{position:absolute;top:0;white-space:nowrap}
.nav .current{color:var(--purple);border-bottom:3px solid var(--purple);padding-bottom:6px}
.quote-btn{left:960px;top:122px;width:155px;height:38px;background:var(--purple);color:var(--white);font-size:13px;font-weight:600;display:flex;align-items:center;justify-content:center;border-radius:2px}

/* hero */
.welcome{left:332px;top:299px;width:538px;height:147px;background:rgba(91,42,147,.88);color:var(--white);text-align:center;font-family:"Poppins",sans-serif}
.welcome p{font-size:30px;margin-top:16px}
.welcome h1{font-size:62px;font-weight:700;line-height:1;margin-top:2px}
.arrow{width:40px;height:40px;border-radius:50%;background:var(--white);display:flex;align-items:center;justify-content:center}
.hero-band{left:0;top:520px;width:1200px;height:220px}
.hero-quote{left:160px;top:633px;width:880px;text-align:center;color:var(--white);font-family:"Poppins",sans-serif;font-style:italic;font-size:20px;line-height:1.5}

/* feature cards */
.promo{width:246px;height:313px;background:linear-gradient(160deg,var(--purple-soft),var(--purple-deep));color:var(--white);text-align:center;padding:56px 10px 0}
.promo h2{font-family:"Poppins",sans-serif;font-weight:600;font-size:25px;margin-bottom:10px}
.promo p{font-size:12.5px;line-height:1.75;white-space:nowrap}
.promo .btn{display:inline-block;margin-top:28px;border:2px solid var(--white);padding:5px 18px;font-size:13px}
.service{top:820px;width:246px}
.service .shot{height:153px}
.service h3{font-family:"Poppins",sans-serif;font-weight:500;font-size:17px;margin:24px 0 10px 12px}
.service p{font-size:11.5px;line-height:1.95;color:var(--body);margin-left:12px;white-space:nowrap}
.more{font-size:12px;color:#444;display:block;margin-top:14px}
.service .more{margin-left:12px}

/* about */
.about-photo{left:0;top:1215px;width:608px;height:397px;background:linear-gradient(90deg,#cfd2dc,#e8e6ec 45%,#d6d8e0)}
.about-panel{left:608px;top:1215px;width:592px;height:397px;background:linear-gradient(135deg,#1c1c1c,#050505);color:var(--white);padding:70px 0 0 31px}
.about-panel h2{font-family:"Poppins",sans-serif;font-weight:500;font-size:32px;margin-bottom:10px}
.about-panel p{font-size:15.5px;line-height:1.78;color:#e6e6e6;white-space:nowrap}
.about-panel .btn{display:inline-flex;align-items:center;justify-content:center;margin-top:14px;width:190px;height:43px;background:var(--purple);border:1px solid #9c79c8;font-family:"Poppins",sans-serif;font-size:17px}

/* news */
.news{width:360px}
.news .date{position:absolute;left:0;top:0;width:48px;height:52px;color:var(--white);text-align:center;font-family:"Poppins",sans-serif}
.news .date b{display:block;font-size:29px;font-weight:600;line-height:40px}
.news .date small{display:block;font-size:7px;line-height:8px}
.news h3{margin-left:70px;font-family:"Poppins",sans-serif;font-weight:400;font-size:17.5px;line-height:1.45}
.news p{margin-left:70px;font-size:11.5px;line-height:1.85;color:var(--body);margin-top:6px;white-space:nowrap}
.news .more{margin-left:70px;margin-top:8px}
.news .more.hot{color:var(--purple)}

/* testimonial */
.testimonial{left:0;top:2126px;width:1200px;height:420px;background:linear-gradient(110deg,#5a2a91,#7444ab 45%,#5d2c95)}
.testimonial h2{position:absolute;left:328px;top:62px;color:var(--white);font-family:"Poppins",sans-serif;font-weight:400;font-size:32px}
.avatar{left:120px;top:2256px;width:136px;height:136px;border-radius:50%;border:4px solid var(--white);background:radial-gradient(circle at 50% 40%,#e8c8a8,#b98a5e)}
.stars{left:135px;top:2405px;display:flex;gap:6px}
.say-text{left:328px;top:2262px;width:780px;color:var(--white);font-size:16px;line-height:1.6;white-space:nowrap}
.say-rule{left:316px;top:2262px;width:2px;height:110px;background:rgba(255,255,255,.6)}
.who{left:328px;top:2354px;color:var(--white);font-family:"Poppins",sans-serif;font-size:26px}
.pager{top:2418px;width:27px;height:27px;display:flex;align-items:center;justify-content:center}

/* footer */
.footer{left:0;top:2520px;width:1200px;height:412px;background:var(--black);color:#cfcfcf}
.footer-brand{left:86px;top:2700px;font-family:"Poppins",sans-serif;font-weight:600;font-size:30px;color:var(--purple-soft);letter-spacing:1px;display:flex;align-items:center;gap:12px}
.footer h4{position:absolute;font-family:"Poppins",sans-serif;font-weight:400;font-size:18px;color:var(--white)}
.f-row{left:363px;display:flex;gap:20px;font-size:13.5px;line-height:1.65;color:#cfcfcf}
.f-row svg{flex:none;margin-top:4px}
.links{left:668px;top:2664px;list-style:none;font-size:12px;line-height:21.2px;color:#cfcfcf}
.links li::before{content:">  ";white-space:pre}
.email-field{left:842px;top:2669px;width:272px;height:52px;border:2px solid #d8d8d8;font-size:12.5px;color:#aaa;padding:16px 0 0 28px}
.submit{left:842px;top:2740px;width:194px;height:48px;background:var(--purple);border:2px solid #cbb6e6;color:var(--white);font-family:"Poppins",sans-serif;font-size:17px;display:flex;align-items:center;justify-content:center}
.f-rule{left:86px;top:2866px;width:1028px;height:1px;background:#3a3a3a}
.copyright{left:86px;top:2886px;font-size:13px;color:#cfcfcf}
</style>
</head>
<body>

<!-- hero photo -->
<div class="abs hero-photo" role="img" aria-label="Electricians at work installing cabling on a building site"></div>

<!-- header -->
<header class="abs header"></header>
<div class="abs brand"><span class="brand-mark"></span>K7 ELECTRICAL</div>

<div class="abs contact-top" style="left:520px">
  <span class="ring"><svg width="18" height="18" viewBox="0 0 24 24"><path fill="#5b2a93" d="M6.6 10.8a15 15 0 0 0 6.6 6.6l2.2-2.2c.3-.3.7-.4 1-.2 1.1.4 2.3.6 3.6.6.6 0 1 .4 1 1V20c0 .6-.4 1-1 1A17 17 0 0 1 3 4c0-.6.4-1 1-1h3.5c.6 0 1 .4 1 1 0 1.3.2 2.5.6 3.6.1.3 0 .7-.2 1z"/></svg></span>
  <div><small>Call K7 Electrical</small><b>+0124 987 650</b></div>
</div>
<div class="abs contact-top" style="left:732px">
  <span class="ring"><svg width="18" height="14" viewBox="0 0 24 18"><rect x="1" y="1" width="22" height="16" rx="1" fill="none" stroke="#5b2a93" stroke-width="2.5"/><path d="M1 2l11 8 11-8" fill="none" stroke="#5b2a93" stroke-width="2.5"/></svg></span>
  <div><small>Mail to</small><b>mail@k7.example</b></div>
</div>
<div class="abs socials" style="left:990px;top:54px" aria-label="Social links"><span></span><span></span><span></span><span></span></div>

<nav class="abs nav">
  <a class="current" href="#" style="left:86px">Home</a>
  <a href="#" style="left:174px">About Us</a>
  <a href="#" style="left:283px">What We Do</a>
  <a href="#" style="left:414px">Team</a>
  <a href="#" style="left:500px">Blog</a>
  <a href="#" style="left:576px">Projects</a>
  <a href="#" style="left:651px">Testimonials</a>
  <a href="#" style="left:813px">Contact Us</a>
</nav>
<a class="abs quote-btn" href="#">Get a free Quote</a>

<!-- hero -->
<div class="abs welcome"><p>Welcome to</p><h1>K7 Electrical</h1></div>
<div class="abs arrow" style="left:48px;top:353px"><svg width="14" height="14" viewBox="0 0 14 14"><path d="M13 7H3M7 2L2 7l5 5" fill="none" stroke="#111" stroke-width="2.4"/></svg></div>
<div class="abs arrow" style="left:1112px;top:353px"><svg width="14" height="14" viewBox="0 0 14 14"><path d="M1 7h10M7 2l5 5-5 5" fill="none" stroke="#111" stroke-width="2.4"/></svg></div>

<svg class="abs hero-band" viewBox="0 0 1200 220" preserveAspectRatio="none" aria-hidden="true">
  <path d="M0 50 C300 -10 700 0 1200 40 L1200 220 L0 220 Z" fill="#5b2a93"/>
  <path d="M0 68 C350 10 750 20 1200 45" fill="none" stroke="#7d52b3" stroke-width="2" opacity=".6"/>
</svg>
<p class="abs hero-quote">"Sed ut perspiciatis unde omnis iste natus error sit voluptatem accusantium doloremque laudantium, totam rem aperiam, eaque ipsa quae".</p>

<!-- what we offer -->
<div class="abs promo" style="left:86px;top:820px">
  <h2>What We Offer?</h2>
  <p>Lorem Ipsum is simply dummy<br>text of the printing and typeset-<br>ting industry. Lorem Ipsum has<br>been the industry's1500s</p>
  <a class="btn" href="#">Read More &gt;</a>
</div>

<article class="abs service" style="left:348px">
  <div class="shot" role="img" aria-label="Hand fitting a wall switch plate" style="background:linear-gradient(135deg,#f1f1ef,#cfcfcb)"></div>
  <h3>Electrical Installations</h3>
  <p>Lorem Ipsum is simply dummy text of<br>the printing and typesetting industry.<br>Lorem Ipsum industry's1500s</p>
  <a class="more" href="#">Read More &gt;</a>
</article>
<article class="abs service" style="left:608px">
  <div class="shot" role="img" aria-label="Warm lit interior with wooden ceiling and pendant lights" style="background:linear-gradient(180deg,#6e4a2c,#b98a58 55%,#4a3a2c)"></div>
  <h3>Lighting Design</h3>
  <p>Lorem Ipsum is simply dummy text of<br>the printing and typesetting industry.<br>Lorem Ipsum industry's1500s</p>
  <a class="more" href="#">Read More &gt;</a>
</article>
<article class="abs service" style="left:868px">
  <div class="shot" role="img" aria-label="Technician in hard hat checking a distribution board" style="background:linear-gradient(135deg,#3a6fb5,#9fb7cf 55%,#e6e6e6)"></div>
  <h3>Electrical Maintenance</h3>
  <p>Lorem Ipsum is simply dummy text of<br>the printing and typesetting industry.<br>Lorem Ipsum industry's1500s</p>
  <a class="more" href="#">Read More &gt;</a>
</article>

<!-- about -->
<div class="abs about-photo" role="img" aria-label="Smiling electrician with coiled cable in front of team members"></div>
<section class="abs about-panel">
  <h2>ABOUT US</h2>
  <p>Sed ut perspiciatis unde omnis iste natus error sit voluptatem<br>accusantium doloremque laudantium, totam rem aperiam,<br>eaque ipsa quae ab illo inventore veritatis et quasi architecto<br>beatae vitae dicta sunt explicabo. Nemo enim ipsam volupta-<br>tem quia voluptas sit aspernatur aut odit aut fugit, sed quia</p>
  <a class="btn" href="#">Meet The Team</a>
</section>

<!-- news -->
<div class="abs promo" style="left:86px;top:1706px;height:322px;padding-top:58px">
  <h2>News &amp; Media</h2>
  <p>Lorem Ipsum is simply dummy<br>text of the printing and typeset-<br>ting industry. Lorem Ipsum has<br>been the industry's1500s</p>
  <a class="btn" href="#">Read More &gt;</a>
</div>

<article class="abs news" style="left:375px;top:1712px">
  <div class="date" style="background:var(--purple)"><b>13</b><small>Feb 2018</small></div>
  <h3>The standard Lorem Ipsum passage, used since the 1500s</h3>
  <p>Lorem ipsum dolor sit amet, consectetur adipi-<br>scing elit, sed do eiusmod tempor incididunt ut<br>labore et dolore magna aliqua.</p>
  <a class="more hot" href="#">Read More &gt;</a>
</article>
<article class="abs news" style="left:770px;top:1712px">
  <div class="date" style="background:var(--grey-date)"><b>12</b><small>Feb 2018</small></div>
  <h3>The standard Lorem Ipsum passage, used since the 1500s</h3>
  <p>Lorem ipsum dolor sit amet, consectetur adipi-<br>scing elit, sed do eiusmod tempor incididunt ut<br>labore et dolore magna aliqua.</p>
  <a class="more" href="#">Read More &gt;</a>
</article>
<article class="abs news" style="left:375px;top:1888px">
  <div class="date" style="background:var(--grey-date)"><b>11</b><small>Feb 2018</small></div>
  <h3>The standard Lorem Ipsum passage, used since the 1500s</h3>
  <p>Lorem ipsum dolor sit amet, consectetur adipi-<br>scing elit, sed do eiusmod tempor incididunt ut<br>labore et dolore magna aliqua.</p>
  <a class="more" href="#">Read More &gt;</a>
</article>
<article class="abs news" style="left:770px;top:1888px">
  <div class="date" style="background:var(--grey-date)"><b>10</b><small>Feb 2018</small></div>
  <h3>The standard Lorem Ipsum passage, used since the 1500s</h3>
  <p>Lorem ipsum dolor sit amet, consectetur adipi-<br>scing elit, sed do eiusmod tempor incididunt ut<br>labore et dolore magna aliqua.</p>
  <a class="more" href="#">Read More &gt;</a>
</article>

<!-- testimonials -->
<section class="abs testimonial"><h2>Thousands Of Happy Customers</h2></section>
<div class="abs avatar" role="img" aria-label="Customer portrait"></div>
<div class="abs stars" aria-label="Five stars">
  <svg width="110" height="18" viewBox="0 0 110 18"><g fill="#f4c21a"><path id="st" d="M9 1l2.4 5.2 5.6.6-4.2 3.8 1.2 5.6L9 13.4 4 16.2l1.2-5.6L1 6.8l5.6-.6z"/><use href="#st" x="22"/><use href="#st" x="44"/><use href="#st" x="66"/><use href="#st" x="88"/></g></svg>
</div>
<div class="abs say-rule"></div>
<p class="abs say-text">"Sed ut perspiciatis unde omnis iste natus error sit voluptatem accusantium doloremque<br>laudantium, totam rem aperiam, eaque ipsa quae ab illo inventore veritatis et quasi architecto<br>beatae vitae dicta sunt explicabo. Nemo enim ipsam &nbsp;aut odit aut fugit, "</p>
<p class="abs who">- Dora L Whitfield</p>
<div class="abs pager" style="left:344px;background:#2a2a2a"><svg width="8" height="10" viewBox="0 0 8 10"><path d="M6 1L2 5l4 4" fill="none" stroke="#fff" stroke-width="1.6"/></svg></div>
<div class="abs pager" style="left:374px;background:#8c8c8c"><svg width="8" height="10" viewBox="0 0 8 10"><path d="M2 1l4 4-4 4" fill="none" stroke="#fff" stroke-width="1.6"/></svg></div>

<!-- footer -->
<footer class="abs footer"></footer>
<svg class="abs" style="left:0;top:2470px" width="1200" height="110" viewBox="0 0 1200 110" preserveAspectRatio="none" aria-hidden="true">
  <path d="M0 30 C300 80 800 90 1200 20 L1200 110 L0 110 Z" fill="#0b0b0b"/>
  <path d="M0 30 C300 80 800 90 1200 20" fill="none" stroke="#ffffff" stroke-width="4"/>
</svg>

<div class="abs footer-brand"><span class="brand-mark" style="background:var(--purple-soft)"></span>K7 ELECTRICAL</div>

<h4 style="left:363px;top:2625px">Contact &nbsp;Info:</h4>
<div class="abs f-row" style="top:2664px">
  <svg width="10" height="14" viewBox="0 0 10 14"><path d="M5 0a5 5 0 0 1 5 5c0 3.5-5 9-5 9S0 8.5 0 5a5 5 0 0 1 5-5z" fill="#cfcfcf"/><circle cx="5" cy="5" r="1.8" fill="#0b0b0b"/></svg>
  <div>K7 Electrical<br>418 Cedarline Avenue, Brookvale,<br>Ohio, 43210.</div>
</div>
<div class="abs f-row" style="top:2752px">
  <svg width="12" height="12" viewBox="0 0 24 24"><path fill="#cfcfcf" d="M6.6 10.8a15 15 0 0 0 6.6 6.6l2.2-2.2c.3-.3.7-.4 1-.2 1.1.4 2.3.6 3.6.6.6 0 1 .4 1 1V20c0 .6-.4 1-1 1A17 17 0 0 1 3 4c0-.6.4-1 1-1h3.5c.6 0 1 .4 1 1 0 1.3.2 2.5.6 3.6.1.3 0 .7-.2 1z"/></svg>
  <div>+0124 987 650</div>
</div>
<div class="abs f-row" style="top:2782px">
  <svg width="13" height="10" viewBox="0 0 24 18"><rect width="24" height="18" rx="1" fill="#cfcfcf"/><path d="M1 2l11 8 11-8" fill="none" stroke="#0b0b0b" stroke-width="2"/></svg>
  <div>mail@k7.example</div>
</div>

<h4 style="left:668px;top:2625px">Quick Links:</h4>
<ul class="abs links">
  <li>Home</li><li>About Us</li><li>What We Do</li><li>Team</li><li>Blog</li><li>Projects</li><li>Testimonials</li><li>Contact Us</li>
</ul>

<h4 style="left:840px;top:2625px">Newsletter Signup</h4>
<div class="abs email-field">Email Address</div>
<div class="abs submit">SUBMIT</div>

<div class="abs f-rule"></div>
<p class="abs copyright">Copyright © 2018. K7 Electrical. All rights reserved.</p>
<div class="abs socials" style="left:990px;top:2888px" aria-label="Social links"><span style="border-color:#cfcfcf"></span><span style="border-color:#cfcfcf"></span><span style="border-color:#cfcfcf"></span><span style="border-color:#cfcfcf"></span></div>

</body>
</html>
```